U.S. Popcorn company needs business cards

We are a popcorn company that manufactures popcorn and sells it to grocery stores worldwide. Our theme is "Americana" and our logo is U.S. route 66 which is the most famous highway in the U.S.

We would like the design to be simple and to use both sides. On the back side we would like to see just the logo and website. The front would be normal details

Target Market(s)

Wholesalers, grocers and distributors

Industry/Entity Type

Manufacture

Contact Information for Business Card

Business name: Prairie Lantern Popcorn
Phone: +1 555 308 4726
Email: Dale@prairielanternpopcorn.com
website: www.prairielanternpopcorn.com
Tag Line: "Fresh off the open road"
Name: Dale Whitcombe
Title: Founder/President

Requirements
Must have
• Either this design should be fun or clean and simple. I will let you show me your thougths.
Nice to have
• Anything that ties in the real Hwy Route 66.
• Colors might need to be red, white and blue incorporated.
Should not have
• Not be too busy.

```html
<!DOCTYPE html>
<html lang="en">
<head>
<meta charset="utf-8">
<title>Prairie Lantern Popcorn – Business Card</title>
<link rel="stylesheet" href="https://fonts.googleapis.com/css2?family=Open+Sans:wght@400;600;700&display=swap">
<style>
  :root {
    --page-bg: #ecebe7;
    --route-red: #e3212b;
    --route-red-deep: #b5121b;
    --route-blue: #1f3f8a;
    --card-white: #ffffff;
    --ray-grey: #dcdbe3;
    --text-white: #ffffff;
  }
  * { box-sizing: border-box; margin: 0; padding: 0; }
  html, body {
    width: 1200px; height: 843px; overflow: hidden;
    background: var(--page-bg);
    font-family: "Open Sans", Arial, sans-serif;
  }
  .card-sheet {
    width: 1200px; height: 843px;
    display: flex; align-items: center; justify-content: center; gap: 40px;
  }
  .card {
    position: relative;
    width: 540px; height: 309px;
    overflow: hidden;
    box-shadow: 0 6px 18px rgba(0,0,0,.18);
  }

  /* Back side */
  .card-back { background: var(--route-red); }
  .card-back .burst {
    position: absolute; inset: 0;
    background: radial-gradient(circle at 50% 50%, #f0444c 0%, var(--route-red) 45%, var(--route-red-deep) 100%);
  }
  .card-back .brand-mark {
    position: absolute; inset: 0;
    display: flex; align-items: center; justify-content: center; gap: 12px;
  }
  .brand-dot {
    width: 18px; height: 18px; border-radius: 50%;
    background: var(--card-white); flex: none;
  }
  .card-back .brand-name {
    color: var(--text-white); font-weight: 700; font-size: 26px; letter-spacing: .5px;
  }

  /* Front side */
  .card-front { background: var(--card-white); }
  .card-front .burst {
    position: absolute; inset: 0;
    background: radial-gradient(circle at 30% 45%, #ffffff 0%, #f6f5f8 40%, var(--ray-grey) 100%);
  }
  .card-front .brand-mark {
    position: absolute; left: 30px; top: 112px; width: 200px;
    display: flex; align-items: center; gap: 10px;
  }
  .card-front .brand-dot { background: var(--route-red); }
  .card-front .brand-name {
    color: var(--route-blue); font-weight: 700; font-size: 20px; line-height: 1.2;
  }

  .info-panel {
    position: absolute; left: 252px; top: 16px; width: 262px; height: 276px;
  }
  .info-panel .shield {
    position: absolute; inset: 0; width: 262px; height: 276px;
  }
  .panel-top {
    position: absolute; left: 0; top: 26px; width: 262px;
    color: var(--text-white); text-align: center;
  }
  .person-name { font-size: 17px; font-weight: 600; letter-spacing: .5px; text-transform: uppercase; line-height: 1.3; }
  .person-title { font-size: 13px; line-height: 1.3; }
  .panel-bottom {
    position: absolute; left: 0; top: 104px; width: 262px;
    color: var(--text-white); padding: 0 24px;
  }
  .contact-list { list-style: none; font-size: 11.5px; line-height: 1.55; }
  .divider { border: 0; border-top: 1px dashed rgba(255,255,255,.75); margin: 12px 0 9px; }
  .tagline { font-size: 14px; font-weight: 600; text-align: center; white-space: nowrap; }
  .stars { text-align: center; font-size: 12px; letter-spacing: 4px; margin-top: 8px; }
</style>
</head>
<body>
  <main class="card-sheet">
    <section class="card card-back" aria-label="Card back">
      <div class="burst" role="img" aria-label="Red sunburst rays background"></div>
      <div class="brand-mark">
        <span class="brand-dot"></span>
        <span class="brand-name">Prairie Lantern Popcorn</span>
      </div>
    </section>

    <section class="card card-front" aria-label="Card front">
      <div class="burst" role="img" aria-label="Soft grey sunburst rays background"></div>
      <div class="brand-mark">
        <span class="brand-dot"></span>
        <span class="brand-name">Prairie Lantern Popcorn</span>
      </div>
      <div class="info-panel">
        <svg class="shield" viewBox="0 0 262 276" aria-hidden="true">
          <defs>
            <clipPath id="shield-outline">
              <path d="M0,22 Q20,22 24,0 L238,0 Q242,22 262,22 L262,150 Q262,240 131,276 Q0,240 0,150 Z"/>
            </clipPath>
          </defs>
          <g clip-path="url(#shield-outline)">
            <rect x="0" y="0" width="262" height="88" fill="var(--route-red)"/>
            <rect x="0" y="88" width="262" height="188" fill="var(--route-blue)"/>
            <line x1="0" y1="88" x2="262" y2="88" stroke="#ffffff" stroke-opacity=".7" stroke-dasharray="4 3"/>
          </g>
        </svg>
        <div class="panel-top">
          <p class="person-name">Dale Whitcombe</p>
          <p class="person-title">Founder/President</p>
        </div>
        <div class="panel-bottom">
          <ul class="contact-list">
            <li>Phone : +1 555 308 4726</li>
            <li>Dale@prairielanternpopcorn.com</li>
            <li>www.prairielanternpopcorn.com</li>
          </ul>
          <hr class="divider">
          <p class="tagline">Fresh off the open road</p>
          <p class="stars">★★★</p>
        </div>
      </div>
    </section>
  </main>
</body>
</html>
```